NEW Modern Sleek Business Card for VR Language Startup

Our startup is using VR to lead the next wave of world language education. We need a two-sided business card that introduces the larger organization (Brightloom Language Inc) and our contact info on one side and shows the product, Glimwoorld, on the other side.

Side 1 (contact info)= Brightloom Logo and Contact info (name, title, phone, email)

Side 2 (product)= Glimworld logo, text, and website
Text= Culturally Immersive Language Learning Games
Website= www.glimworld-play.com

Target Market(s)

Education, Technology

Contact Information for Business Card

Contact info will be updated upon approval of the design. For now, put this as a placeholder.

Perry Dunmore
Founder & CEO
pdunmore@quillpost-mail.net
(555)-014-2286

Font styles to use
Other font styles liked:
• Gibson and Century Gothic are the brand fonts

Requirements
Nice to have
• I would love to see cohesion between the design and colors of the two logos. I have attached a few business card designs that I like, so you can get a feel for my preferred style.

```html
<!DOCTYPE html>
<html lang="en">
<head>
<meta charset="utf-8">
<title>Brightloom Language – Business Card</title>
<link href="https://fonts.googleapis.com/css2?family=Montserrat:wght@500;600;700&family=Lato:wght@400;700&display=swap" rel="stylesheet">
<style>
  :root {
    --bg: #6a6a6a;
    --paper: #fbfbfa;
    --ink: #1f1f1f;
    --ink-soft: #555555;
    --accent-red: #e8173d;
    --mark: #e2445a;
    --cyan: #3fd6ea;
    --orange: #f39a2b;
    --coral: #f0414e;
    --violet: #8a5ce0;
    --blue: #5a72ea;
    --panel-top: #6fcde9;
    --panel-mid: #9a7be2;
    --panel-low: #6f73e6;
    --white: #ffffff;
  }
  * { box-sizing: border-box; margin: 0; padding: 0; }
  html, body {
    width: 1200px; height: 1056px; overflow: hidden;
    background: var(--bg);
  }
  .stage {
    position: relative; width: 1200px; height: 1056px;
  }
  .card {
    position: absolute; left: 200px; width: 800px; height: 457px;
    background: var(--paper);
    box-shadow: 0 10px 24px rgba(0,0,0,0.35);
    overflow: hidden;
  }
  .card--front { top: 52px; }
  .card--back { top: 548px; }
  .card__art { position: absolute; inset: 0; width: 100%; height: 100%; }

  .brand { position: absolute; display: flex; align-items: center; gap: 18px; }
  .brand__dot { border-radius: 50%; background: var(--mark); flex: none; }
  .brand__name {
    font-family: "Montserrat", sans-serif; font-weight: 600;
    color: var(--ink); line-height: 1.15; letter-spacing: 0.16em;
    text-transform: uppercase;
  }
  .card--front .brand { left: 70px; top: 160px; }
  .card--front .brand__dot { width: 84px; height: 84px; }
  .card--front .brand__name { font-size: 27px; }
  .card--back .brand { left: 62px; top: 82px; }
  .card--back .brand__dot { width: 70px; height: 70px; }
  .card--back .brand__name { font-size: 23px; }

  .contact {
    position: absolute; left: 540px; top: 158px;
    font-family: "Lato", sans-serif; color: var(--ink);
  }
  .contact__name { font-size: 27px; font-weight: 700; color: var(--accent-red); }
  .contact__title { font-size: 17px; margin-top: 4px; }
  .contact__list { list-style: none; margin-top: 14px; }
  .contact__item { display: flex; align-items: center; gap: 12px; font-size: 15.5px; margin-top: 6px; }
  .contact__icon { width: 14px; height: 14px; fill: var(--accent-red); flex: none; }

  .website {
    position: absolute; left: 110px; bottom: 62px;
    font-family: "Lato", sans-serif; font-size: 16px; color: var(--ink);
    letter-spacing: 0.02em;
  }
  .tagline {
    position: absolute; right: 48px; top: 50%; transform: translateY(-50%);
    font-family: "Montserrat", sans-serif; font-weight: 700;
    font-size: 31px; line-height: 1.22; color: var(--white);
    text-align: right; letter-spacing: 0.03em; text-transform: uppercase;
  }
</style>
</head>
<body>
<main class="stage">

  <section class="card card--front" aria-label="Contact side">
    <svg class="card__art" viewBox="0 0 800 457" aria-hidden="true">
      <defs>
        <linearGradient id="wedge-warm" x1="0" y1="0" x2="0" y2="1">
          <stop offset="0" stop-color="var(--orange)"/>
          <stop offset="0.35" stop-color="var(--coral)"/>
          <stop offset="0.7" stop-color="var(--violet)"/>
          <stop offset="1" stop-color="var(--blue)"/>
        </linearGradient>
      </defs>
      <polygon points="372,0 432,0 438,190" fill="var(--cyan)"/>
      <polygon points="432,0 490,0 430,457 424,457" fill="url(#wedge-warm)"/>
    </svg>

    <div class="brand">
      <span class="brand__dot"></span>
      <p class="brand__name">Brightloom<br>Language</p>
    </div>

    <div class="contact">
      <h1 class="contact__name">Perry Dunmore</h1>
      <p class="contact__title">Founder &amp; CEO</p>
      <ul class="contact__list">
        <li class="contact__item">
          <svg class="contact__icon" viewBox="0 0 24 24"><path d="M6.6 10.8a15.1 15.1 0 0 0 6.6 6.6l2.2-2.2a1 1 0 0 1 1-.25 11.4 11.4 0 0 0 3.6.57 1 1 0 0 1 1 1V20a1 1 0 0 1-1 1A17 17 0 0 1 3 4a1 1 0 0 1 1-1h3.5a1 1 0 0 1 1 1c0 1.25.2 2.45.57 3.57a1 1 0 0 1-.25 1z"/></svg>
          <span>(555)-014-2286</span>
        </li>
        <li class="contact__item">
          <svg class="contact__icon" viewBox="0 0 24 24"><path d="M2 5h20v14H2z M2 5l10 8 10-8" /><path d="M3 6l9 7 9-7" stroke="var(--paper)" stroke-width="2" fill="none"/></svg>
          <span>pdunmore@quillpost-mail.net</span>
        </li>
      </ul>
    </div>
  </section>

  <section class="card card--back" aria-label="Product side">
    <svg class="card__art" viewBox="0 0 800 457" aria-hidden="true">
      <defs>
        <linearGradient id="panel-fill" x1="1" y1="0" x2="0" y2="1">
          <stop offset="0" stop-color="var(--panel-top)"/>
          <stop offset="0.5" stop-color="var(--panel-mid)"/>
          <stop offset="1" stop-color="var(--panel-low)"/>
        </linearGradient>
        <linearGradient id="edge-fill" x1="0" y1="0" x2="0" y2="1">
          <stop offset="0" stop-color="var(--cyan)"/>
          <stop offset="1" stop-color="var(--blue)"/>
        </linearGradient>
      </defs>
      <polygon points="418,0 800,0 800,457 398,457" fill="url(#panel-fill)"/>
      <polygon points="418,0 432,0 452,320 398,457" fill="url(#edge-fill)" opacity="0.85"/>
      <polygon points="440,300 520,457 420,457" fill="var(--cyan)" opacity="0.9"/>
    </svg>

    <div class="brand">
      <span class="brand__dot"></span>
      <p class="brand__name">Brightloom<br>Language</p>
    </div>

    <p class="website">www.glimworld-play.com</p>

    <h2 class="tagline">Culturally<br>Immersive<br>Language<br>Learning<br>Games</h2>
  </section>

</main>
</body>
</html>
```